Logo, Web and Mobile Designs for enterprise social media platform

All the details are in the attached document, please start reading the scope document first which explains what is this project about and the details about the needed deliverables, after that please read the UI_Requirements document which will detail what is expected regarding the coded web version since this is a coded contest, it is very important that you meet the UI requirements or suggest something else but we will need to agree first before working on the coded version

Good Luck

Target Market(s)

Enterprise Social Media

Industry/Entity Type

Media

Coding

Coded - Design and coding required

Number of Pages Required

5+ page

Font styles to use
Sans Serif

Requirements
Must have
• All the must haves are listed in the scope document so please check before you start

```html
<!DOCTYPE html>
<html lang="en">
<head>
<meta charset="utf-8">
<title>Teamvana – Enterprise Social Network</title>
<link rel="stylesheet" href="https://fonts.googleapis.com/css2?family=Hind:wght@400;500;600&family=Open+Sans:wght@400;600&display=swap">
<style>
  :root {
    --brand-blue: #0a72c4;
    --button-top: #22a3f0;
    --button-bottom: #0a6fc7;
    --topbar-bg: #454545;
    --footer-bg: #3d3d3d;
    --topbar-text: #e6e6e6;
    --footer-text: #bdbdbd;
    --nav-text: #3a3a3a;
    --headline: #333333;
    --body-text: #2e2e2e;
    --white: #ffffff;
    --field-border: #c9c9c9;
    --icon-grey: #c4c4c4;
    --social-grey: #8e8e8e;
  }
  * { box-sizing: border-box; margin: 0; padding: 0; }
  html, body { width: 1200px; height: 692px; overflow: hidden; }
  body { position: relative; font-family: "Open Sans", Arial, sans-serif; background: var(--white); }

  .utility-bar { position: absolute; top: 0; left: 0; width: 1200px; height: 39px; background: var(--topbar-bg); }
  .utility-icons { position: absolute; left: 99px; top: 13px; display: flex; gap: 15px; }
  .utility-icons svg { width: 13px; height: 13px; fill: var(--icon-grey); }
  .utility-links { position: absolute; right: 100px; top: 0; height: 39px; display: flex; align-items: center; gap: 25px; font-size: 12.5px; color: var(--topbar-text); }
  .utility-links .has-menu svg { margin-left: 9px; width: 8px; height: 8px; stroke: var(--topbar-text); fill: none; stroke-width: 1.5; }

  .site-header { position: absolute; top: 39px; left: 0; width: 1200px; height: 79px; background: var(--white); border-bottom: 1px solid #d8d8d8; }
  .brand-name { position: absolute; left: 99px; top: 22px; font-family: "Hind", Arial, sans-serif; font-weight: 500; font-size: 31px; line-height: 1; color: var(--brand-blue); }
  .main-nav { position: absolute; right: 100px; top: 0; height: 79px; display: flex; align-items: center; gap: 40px; font-size: 12.5px; color: var(--nav-text); }
  .main-nav .active { color: var(--brand-blue); }
  .main-nav .has-menu svg { margin-left: 9px; width: 8px; height: 8px; stroke: var(--nav-text); fill: none; stroke-width: 1.5; }
  .main-nav .nav-split { display: flex; gap: 32px; }

  .hero { position: absolute; top: 118px; left: 0; width: 1200px; height: 482px;
    background: linear-gradient(90deg, #aeb9c1 0%, #c3ccd2 35%, #d6dde0 55%, #8b93a8 70%, #6f78a8 85%, #9aa6c2 100%); }
  .hero-title { position: absolute; left: 99px; top: 86px; font-family: "Hind", Arial, sans-serif; font-weight: 500; font-size: 30px; line-height: 43px; color: var(--headline); }
  .hero-lead { position: absolute; left: 99px; top: 176px; width: 460px; font-size: 12px; line-height: 21px; color: var(--body-text); }

  .signup-card { position: absolute; left: 99px; top: 240px; width: 415px; height: 146px; background: var(--white); border-radius: 3px; }
  .signup-title { position: absolute; left: 22px; top: 24px; font-size: 12.5px; color: var(--brand-blue); }
  .email-field { position: absolute; left: 19px; top: 56px; width: 276px; height: 45px; border: 1px solid var(--field-border); font: 12.5px "Open Sans", Arial, sans-serif; color: #666; padding-left: 10px; display: flex; align-items: center; }
  .signup-button { position: absolute; left: 304px; top: 56px; width: 90px; height: 45px; border: none; background: linear-gradient(180deg, var(--button-top), var(--button-bottom)); color: var(--white); font: 600 16px "Hind", Arial, sans-serif; display: flex; align-items: center; justify-content: center; }
  .signup-note { position: absolute; left: 23px; top: 111px; font-size: 10.5px; color: var(--body-text); display: flex; align-items: center; gap: 8px; }
  .signup-note svg { width: 9px; height: 10px; fill: #222; }

  .slide-dots { position: absolute; left: 101px; top: 420px; display: flex; gap: 9px; }
  .slide-dots span { width: 6px; height: 6px; border-radius: 50%; background: var(--white); }
  .slide-dots .current { background: var(--brand-blue); }

  .site-footer { position: absolute; top: 600px; left: 0; width: 1200px; height: 92px; background: var(--footer-bg); }
  .footer-nav { position: absolute; left: 99px; top: 30px; display: flex; gap: 40px; font-size: 12.5px; color: var(--footer-text); }
  .copyright { position: absolute; left: 99px; top: 54px; font-size: 12.5px; color: var(--footer-text); }
  .social-links { position: absolute; right: 105px; top: 34px; display: flex; gap: 16px; }
  .social-links span { width: 14px; height: 14px; border-radius: 50%; background: var(--social-grey); }
</style>
</head>
<body>
  <div class="utility-bar">
    <div class="utility-icons">
      <svg viewBox="0 0 12 12" aria-label="User"><circle cx="6" cy="3.2" r="2.7"/><path d="M1 12c0-3.5 2.2-5 5-5s5 1.5 5 5z"/></svg>
      <svg viewBox="0 0 14 12" aria-label="Messages"><ellipse cx="5.5" cy="4.5" rx="5.2" ry="3.8"/><path d="M2 7l-1 3 3-2z"/><ellipse cx="9.5" cy="7.5" rx="4" ry="3" opacity=".85"/></svg>
      <svg viewBox="0 0 12 12" aria-label="Language"><circle cx="6" cy="6" r="5.6"/></svg>
    </div>
    <nav class="utility-links">
      <span>Home</span>
      <span>Profile</span>
      <span class="has-menu">Account<svg viewBox="0 0 8 8"><path d="M1 2.5l3 3 3-3"/></svg></span>
    </nav>
  </div>

  <header class="site-header">
    <div class="brand-name">Teamvana</div>
    <nav class="main-nav">
      <span class="active">Home</span>
      <span>Events</span>
      <span class="nav-split">
        <span class="has-menu">Business Opportunities<svg viewBox="0 0 8 8"><path d="M1 2.5l3 3 3-3"/></svg></span>
        <span class="has-menu">Feature Article<svg viewBox="0 0 8 8"><path d="M1 2.5l3 3 3-3"/></svg></span>
      </span>
      <span>Support</span>
      <span>Contact</span>
    </nav>
  </header>

  <section class="hero" role="img" aria-label="Photo of a smiling man in a striped shirt working on a laptop in a bright office">
    <h1 class="hero-title">The World Moves Fast.<br>Move Faster With Teamvana</h1>
    <p class="hero-lead">Neque porro quisquam est, qui dolorem ipsum quia dolor sit amet, consectetur, adipisci velit, sed quia non numquam</p>

    <form class="signup-card">
      <p class="signup-title">Join Your Company's Social Network for Free</p>
      <div class="email-field">Enter Your Mail Address</div>
      <div class="signup-button">Sign Up</div>
      <p class="signup-note"><svg viewBox="0 0 9 10"><path d="M2 4V3a2.5 2.5 0 0 1 5 0v1h1v6H1V4zm1 0h3V3a1.5 1.5 0 0 0-3 0z"/></svg>Only people with a verified company email address can join the network</p>
    </form>

    <div class="slide-dots"><span class="current"></span><span></span><span></span></div>
  </section>

  <footer class="site-footer">
    <nav class="footer-nav">
      <span>Home</span><span>Events</span><span>Business Opportunities</span><span>Feature Article</span><span>Support</span><span>Contact</span>
    </nav>
    <p class="copyright">© Copyright 2015 Teamvana. All rights reserved.</p>
    <div class="social-links" aria-label="Social links"><span></span><span></span><span></span><span></span><span></span></div>
  </footer>
</body>
</html>
```